Birchline Septic Solutions

Would like to see some single sided ones but would also like to see some double sided with one sided only being the logo. Owners name is Colin Vandro. Phone number is 555-214-0387
Services are pumping, inspections, installs, and repairs

Contact Information for Business Card

555-241-0387 Colin Vandro Lindenvale, NV

```html
<!DOCTYPE html>
<html lang="en">
<head>
<meta charset="utf-8">
<title>Birchline Septic Solutions – Business Cards</title>
<link rel="stylesheet" href="https://fonts.googleapis.com/css2?family=Montserrat:wght@400;500;700;800&display=swap">
<style>
  :root {
    --teal: #12bdb6;
    --ink: #161616;
    --paper: #ffffff;
    --backdrop: #e9ecec;
  }
  * { box-sizing: border-box; margin: 0; padding: 0; }
  html, body {
    width: 1200px; height: 960px; overflow: hidden;
    background: var(--backdrop);
    font-family: "Montserrat", sans-serif;
  }
  .canvas { position: relative; width: 1200px; height: 960px; }
  .card {
    position: absolute; left: 250px;
    width: 700px; height: 400px;
    border-radius: 26px;
    box-shadow: 0 10px 30px rgba(0,0,0,.15);
  }
  .card--front { top: 50px; background: var(--teal); color: var(--paper);
    display: flex; flex-direction: column; align-items: center; justify-content: center; text-align: center; }
  .card--back { top: 500px; background: var(--paper); color: var(--ink); }

  .brand-name { font-weight: 800; text-transform: uppercase; letter-spacing: .06em; line-height: 1.1; }
  .card--front .brand-name { font-size: 42px; color: var(--paper); }
  .card--front .brand-name span { display: block; font-size: 22px; letter-spacing: .32em; margin-top: 10px; }

  .services { margin-top: 42px; font-size: 22px; font-weight: 500; line-height: 1.5; }
  .services .tick { display: inline-block; width: 18px; height: 18px; vertical-align: -2px; margin: 0 4px; }

  .card--back .brand-name {
    position: absolute; left: 50px; top: 150px; width: 270px;
    font-size: 34px; color: var(--ink);
  }
  .card--back .brand-name span { display: block; font-size: 15px; letter-spacing: .3em; margin-top: 12px; }
  .divider { position: absolute; left: 345px; top: 110px; width: 2px; height: 180px; background: var(--teal); }
  .contact { position: absolute; left: 372px; top: 118px; white-space: nowrap; }
  .contact__name { font-size: 28px; font-weight: 800; text-transform: uppercase; letter-spacing: .01em; }
  .contact__name .accent { color: var(--teal); }
  .contact__role { font-size: 18px; margin-top: 4px; font-weight: 500; }
  .contact__line { display: flex; align-items: center; gap: 10px; font-size: 18px; margin-top: 14px; font-weight: 500; }
  .contact__line svg { width: 18px; height: 18px; flex: none; }
</style>
</head>
<body>
<main class="canvas">
  <section class="card card--front">
    <div class="brand-name">Birchline<span>Septic Solutions</span></div>
    <p class="services">
      <svg class="tick" viewBox="0 0 20 20"><circle cx="10" cy="10" r="8" fill="none" stroke="#fff" stroke-width="2"/><path d="M6 10l3 3 5-6" fill="none" stroke="#fff" stroke-width="2"/></svg>Services are pumping<br>
      <svg class="tick" viewBox="0 0 20 20"><circle cx="10" cy="10" r="8" fill="none" stroke="#fff" stroke-width="2"/><path d="M6 10l3 3 5-6" fill="none" stroke="#fff" stroke-width="2"/></svg>inspections
      <svg class="tick" viewBox="0 0 20 20"><circle cx="10" cy="10" r="8" fill="none" stroke="#fff" stroke-width="2"/><path d="M6 10l3 3 5-6" fill="none" stroke="#fff" stroke-width="2"/></svg>installs
      <svg class="tick" viewBox="0 0 20 20"><circle cx="10" cy="10" r="8" fill="none" stroke="#fff" stroke-width="2"/><path d="M6 10l3 3 5-6" fill="none" stroke="#fff" stroke-width="2"/></svg>and repairs
    </p>
  </section>

  <section class="card card--back">
    <div class="brand-name">Birchline<span>Septic Solutions</span></div>
    <div class="divider"></div>
    <div class="contact">
      <h1 class="contact__name">Colin <span class="accent">Vandro</span></h1>
      <p class="contact__role">Owners</p>
      <p class="contact__line">
        <svg viewBox="0 0 24 24"><path fill="#12bdb6" d="M6.6 10.8a15.1 15.1 0 006.6 6.6l2.2-2.2c.3-.3.7-.4 1-.2 1.1.4 2.3.6 3.6.6.6 0 1 .4 1 1V20c0 .6-.4 1-1 1A17 17 0 013 4c0-.6.4-1 1-1h3.5c.6 0 1 .4 1 1 0 1.3.2 2.5.6 3.6.1.3 0 .7-.2 1z"/></svg>
        555-214-0387
      </p>
      <p class="contact__line">
        <svg viewBox="0 0 24 24"><path fill="#12bdb6" d="M12 2a7 7 0 00-7 7c0 5.2 7 13 7 13s7-7.8 7-13a7 7 0 00-7-7zm0 9.5A2.5 2.5 0 1112 6.5a2.5 2.5 0 010 5z"/></svg>
        Colin Vandro Lindenvale, NV
      </p>
    </div>
  </section>
</main>
</body>
</html>
```